Laser Tattoo Removal Business Cards

We are looking for a professional business card design for a laser tattoo removal business. Ideally looking for a black business card design. The name of the business is Brightline Tattoo Removal. We place our cards at local tattoo shops so we ideally are looking for something trendy/edgy to draw both male and female clientele in.

Target Market(s)

Male/Female ages 18-60

Contact Information for Business Card

black background ideally.. hoping to stay within greys, whites and black

Font styles to use
Serif
Sans Serif

Colors
121212
a9a9a9
5c5c5c
f5f5f5
ffffff
7f7f7f
606060
848484
9d9d9d

Requirements
Must have
• Employee Info:
• Melissa Thornbury
• Chief Executive Offer
• m: 919.537.2846
• w: 919.362.4178
• f: 919.685.3907
• mthornbury@brightlinetattooremoval.example
• Address:
• 4615 Oakmere Pkwy, Suite 210
• Raleigh, NC 27654
• Website:
• www.brightlinetattooremoval.example
Nice to have
• Myabe business name on back or logo on back and employee info on the front

```html
<!DOCTYPE html>
<html lang="en">
<head>
<meta charset="utf-8">
<title>Brightline Tattoo Removal – Business Cards</title>
<link rel="stylesheet" href="https://fonts.googleapis.com/css2?family=Josefin+Sans:wght@400&family=Lato:wght@400;700&display=swap">
<style>
  :root {
    --ink: #121212;
    --paper: #f5f5f5;
    --white: #ffffff;
    --grey-light: #a9a9a9;
    --grey-mid: #7f7f7f;
    --grey-dark: #5c5c5c;
    --backdrop: #2b2b2b;
  }
  * { box-sizing: border-box; margin: 0; padding: 0; }
  html, body { width: 1200px; height: 900px; overflow: hidden; }
  body {
    background: var(--backdrop);
    font-family: "Lato", sans-serif;
    position: relative;
  }
  .card {
    position: absolute;
    left: 280px;
    width: 640px;
    height: 366px;
    border-radius: 14px;
    overflow: hidden;
    background: var(--ink);
    box-shadow: 0 10px 30px rgba(0,0,0,.45);
  }
  .card--brand { top: 60px; }
  .card--contact { top: 474px; display: flex; }

  .wordmark {
    font-family: "Josefin Sans", sans-serif;
    font-weight: 400;
    text-align: center;
    text-transform: uppercase;
  }
  .wordmark__name { display: block; font-size: 52px; letter-spacing: 4px; line-height: 1; }
  .wordmark__trade { display: block; font-size: 20px; letter-spacing: 5px; margin-top: 16px; }
  .wordmark__trade::before, .wordmark__trade::after { content: "—"; margin: 0 10px; }
  .wordmark__dot { display: inline-block; width: 12px; height: 12px; background: currentColor; margin-top: 14px; }

  .card--brand .wordmark { color: var(--white); position: absolute; top: 88px; left: 0; right: 0; }
  .website {
    position: absolute; bottom: 62px; left: 0; right: 0;
    text-align: center; color: var(--white);
    font-size: 15px; letter-spacing: 3px;
  }

  .panel-light {
    width: 268px; height: 100%; flex: none;
    background: var(--paper);
    display: flex; align-items: center; justify-content: center;
  }
  .panel-light .wordmark { color: var(--ink); }
  .panel-light .wordmark__name { font-size: 31px; letter-spacing: 3px; }
  .panel-light .wordmark__trade { font-size: 12px; letter-spacing: 3px; margin-top: 12px; }
  .panel-light .wordmark__dot { width: 9px; height: 9px; }

  .divider { display: flex; height: 100%; flex: none; }
  .divider span { display: block; height: 100%; }
  .divider .bar-dark { width: 7px; background: var(--ink); }
  .divider .bar-light { width: 5px; background: var(--white); }
  .divider .gap { width: 4px; background: var(--paper); }

  .details { flex: 1; min-width: 0; padding: 42px 14px 0 30px; color: var(--white); }
  .person__name { font-size: 21px; font-weight: 400; }
  .person__name b { font-weight: 700; }
  .person__title { font-size: 13px; color: var(--grey-light); margin-top: 4px; }
  .address { font-size: 15px; font-weight: 700; line-height: 1.4; margin-top: 50px; }
  .contact-list { list-style: none; margin-top: 12px; font-size: 13px; color: var(--paper); }
  .contact-list li { display: flex; align-items: center; gap: 10px; margin-bottom: 8px; white-space: nowrap; }
  .contact-list .contact-list__email { font-size: 12px; }
  .contact-list svg { width: 15px; height: 13px; fill: var(--white); flex: none; }
</style>
</head>
<body>

  <section class="card card--brand" aria-label="Card back">
    <div class="wordmark">
      <span class="wordmark__name">Brightline</span>
      <span class="wordmark__dot"></span>
      <span class="wordmark__trade">Tattoo Removal</span>
    </div>
    <p class="website">www.brightlinetattooremoval.example</p>
  </section>

  <section class="card card--contact" aria-label="Card front">
    <div class="panel-light">
      <div class="wordmark">
        <span class="wordmark__name">Brightline</span>
        <span class="wordmark__dot"></span>
        <span class="wordmark__trade">Tattoo Removal</span>
      </div>
    </div>
    <div class="divider" aria-hidden="true">
      <span class="bar-dark"></span><span class="gap"></span>
      <span class="bar-dark"></span><span class="bar-light"></span>
      <span class="bar-dark"></span><span class="bar-light"></span>
    </div>
    <div class="details">
      <h1 class="person__name">Melissa <b>Thornbury</b></h1>
      <p class="person__title">Chief Executive Offer</p>
      <p class="address">4615 Oakmere Pkwy, Suite 210<br>Raleigh, NC 27654</p>
      <ul class="contact-list">
        <li>
          <svg viewBox="0 0 16 14" aria-hidden="true"><path d="M1 5c0-3 4-4 7-4s7 1 7 4l-3 1-1-2H5L4 6zM3 7h10l1 6H2z"/></svg>
          m: 919.537.2846
        </li>
        <li>
          <svg viewBox="0 0 16 14" aria-hidden="true"><path d="M1 5c0-3 4-4 7-4s7 1 7 4l-3 1-1-2H5L4 6zM3 7h10l1 6H2z"/></svg>
          w: 919.362.4178
        </li>
        <li>
          <svg viewBox="0 0 16 14" aria-hidden="true"><path d="M4 0h8v4H4zM1 5h14v6h-3v3H4v-3H1zM5 9v4h6V9z"/></svg>
          f: 919.685.3907
        </li>
        <li class="contact-list__email">
          <svg viewBox="0 0 16 14" aria-hidden="true"><path d="M0 2h16v10H0zM1.5 3.2v.6L8 8l6.5-4.2v-.6z" fill-rule="evenodd"/></svg>
          mthornbury@brightlinetattooremoval.example
        </li>
      </ul>
    </div>
  </section>

</body>
</html>
```